Lo Mara Menu Design Project

This project is pretty straight forward. You will be given 3 files which include the following:
1. Our proposed menu
2. Our Company logo
3. A sample menu on what we are looking for design wise

Your job is to create a visually pleasing menu that is simple, clean and fresh. Please refer to our home website for additional information. (www.lomara-eats.com) Must be in eps or equivalent format.

Target Market(s)

20s to 40s

Industry/Entity Type

It Company

Requirements
Must have
• Company log
Must be in EPS format

```html
<!DOCTYPE html>
<html lang="en">
<head>
<meta charset="utf-8">
<title>Lo Mara — Beef &amp; Pork / Seafood Menu</title>
<link rel="stylesheet" href="https://fonts.googleapis.com/css2?family=Poppins:ital,wght@0,400;0,600;1,300;1,600&display=swap">
<style>
  :root {
    --bg: #000000;
    --accent: #c8232b;
    --ink: #ffffff;
    --ornament-core: #5a0a0f;
    --ornament-edge: rgba(60, 6, 10, 0);
  }
  html, body {
    margin: 0;
    padding: 0;
    overflow: hidden;
    background: var(--bg);
  }
  .menu {
    position: relative;
    width: 1200px;
    height: 1000px;
    background: var(--bg);
    color: var(--ink);
    font-family: "Poppins", "Century Gothic", sans-serif;
    overflow: hidden;
  }
  .menu__ornament {
    position: absolute;
    left: 140px;
    top: 170px;
    width: 960px;
    height: 740px;
  }
  .menu__divider {
    position: absolute;
    left: 599px;
    top: 48px;
    width: 3px;
    height: 898px;
    background: var(--accent);
  }
  .section {
    position: absolute;
    top: 28px;
  }
  .section--beef { left: 50px; width: 505px; }
  .section--seafood { left: 655px; width: 493px; }
  .section__title {
    margin: 0 0 14px;
    text-align: center;
    color: var(--accent);
    font-weight: 400;
    font-size: 27px;
    letter-spacing: 0.5px;
  }
  .section__notes {
    margin: 0 0 24px;
    text-align: center;
    font-style: italic;
    font-weight: 300;
    font-size: 18px;
    line-height: 23px;
  }
  .section--seafood .section__notes { margin-bottom: 14px; }
  .dish { margin: 0 0 4px; }
  .section--beef .dish { margin-bottom: 6px; }
  .dish__head {
    display: flex;
    justify-content: space-between;
    font-weight: 600;
    font-size: 17.5px;
    line-height: 23px;
    letter-spacing: 0.3px;
  }
  .dish__desc {
    margin: 0;
    text-align: right;
    font-style: italic;
    font-weight: 300;
    font-size: 17.5px;
    line-height: 23px;
  }
  .dish__desc--featured { font-weight: 600; }
  .brand {
    position: absolute;
    top: 934px;
    display: flex;
    align-items: center;
    gap: 5px;
    color: var(--accent);
    font-weight: 600;
    font-size: 14px;
    letter-spacing: 0.5px;
  }
  .brand--left { left: 16px; }
  .brand--right { right: 16px; }
  .brand__mark {
    width: 10px;
    height: 10px;
    background: var(--accent);
  }
</style>
</head>
<body>
<main class="menu">
  <svg class="menu__ornament" role="img" aria-label="Large dark red decorative cloud ornament in the background" viewBox="0 0 960 740">
    <defs>
      <radialGradient id="ornamentGlow" cx="50%" cy="45%" r="55%">
        <stop offset="0%" stop-color="var(--ornament-core)" style="stop-color:#5a0a0f"/>
        <stop offset="70%" stop-color="#3e070b"/>
        <stop offset="100%" stop-color="#000000" stop-opacity="0"/>
      </radialGradient>
    </defs>
    <ellipse cx="480" cy="350" rx="470" ry="370" fill="url(#ornamentGlow)"/>
  </svg>

  <div class="menu__divider"></div>

  <section class="section section--beef">
    <h2 class="section__title">BEEF &amp; PORK</h2>
    <p class="section__notes">Rice is not included. Add rice $1.25.<br>Enjoy a Half Chinese Chicken Salad or Plain Fried<br>Rice with any entrée for $5.50<br>Can replace Beef/Pork with Tofu for $1.50</p>

    <div class="dish"><div class="dish__head"><span>Mongolian Beef</span><span>12.25</span></div>
      <p class="dish__desc">Flank steak, garlic, ginger, and green onions on a<br>bed of white crunchies.</p></div>
    <div class="dish"><div class="dish__head"><span>Beef And Broccoli</span><span>11.95</span></div>
      <p class="dish__desc">Flank steak, broccoli, and black mushrooms sautéed<br>in a garlic brown sauce.</p></div>
    <div class="dish"><div class="dish__head"><span>Pepper Steak</span><span>11.95</span></div>
      <p class="dish__desc">Flank steak, bell peppers, onions, and garlic in black<br>pepper sauce.</p></div>
    <div class="dish"><div class="dish__head"><span>Sliced Barbequed Pork</span><span>8.95</span></div>
      <p class="dish__desc dish__desc--featured">Tender slices of juicy pork topped with scallions<br>in a barbeque sauce.</p></div>
    <div class="dish"><div class="dish__head"><span>Barbequed Spareribs</span><span>8.95</span></div>
      <p class="dish__desc">Slow-Roasted juicy pork ribs with barbeque sauce.</p></div>
    <div class="dish"><div class="dish__head"><span>Tangerine Beef</span><span>12.25</span></div>
      <p class="dish__desc">Crisp flank steak topped with scallions in a tangerine<br>sauce.</p></div>
    <div class="dish"><div class="dish__head"><span>Spicy Garlic Tomato Beef</span><span>12.95</span></div>
      <p class="dish__desc">Flank steak, tomato, water chestnuts, zucchini, onions,<br>and spicy garlic sauce.</p></div>
    <div class="dish"><div class="dish__head"><span>Ma Pao Tofu</span><span>7.95</span></div>
      <p class="dish__desc">Soft tofu cubes with ground pork or chicken cooked<br>in Szechuan-Style sauce.</p></div>
  </section>

  <section class="section section--seafood">
    <h2 class="section__title">SEAFOOD</h2>
    <p class="section__notes">Enjoy a Half Chinese Chicken Salad or Plain Fried<br>Rice with any entrée for $5.50<br>Can replace Seafood with Tofu for $1.50</p>

    <div class="dish"><div class="dish__head"><span>Crispy Spicy Honey Shrimp</span><span>13.95</span></div>
      <p class="dish__desc">Crispy large shrimp with red bell peppers, scallions,<br>and chili peppers in a sweet honey sauce.</p></div>
    <div class="dish"><div class="dish__head"><span>Kung Pao Three Treasures</span><span>13.95</span></div>
      <p class="dish__desc">Large shrimp, beef, and chicken breast with scal-<br>lions, peanuts, water chestnuts, and chili peppers.<br>Prepared mandarin-Style.</p></div>
    <div class="dish"><div class="dish__head"><span>Honey Walnut Shrimp</span><span>13.95</span></div>
      <p class="dish__desc">Lightly crisped savory shrimp with honey-Glazed<br>walnuts.</p></div>
    <div class="dish"><div class="dish__head"><span>Fish With Ginger Soy Sauce</span><span>15.95</span></div>
      <p class="dish__desc">Whole white fish filet steamed with ginger and<br>topped with green onions and cilantro.</p></div>
    <div class="dish"><div class="dish__head"><span>Shrimp With Snow Peas</span><span>13.95</span></div>
      <p class="dish__desc">Large shrimp with snow peas, water chestnuts,<br>carrots, and ginger in a white wine sauce.</p></div>
    <div class="dish"><div class="dish__head"><span>Shrimp With Lobster Sauce</span><span>13.95</span></div>
      <p class="dish__desc">Large shrimp, eggs, ground pork, snow peas, water<br>chestnuts, and red bell peppers sautéed in a lob-<br>ster sauce.</p></div>
    <div class="dish"><div class="dish__head"><span>Salt And Pepper Shrimp</span><span>13.95</span></div>
      <p class="dish__desc">Lightly battered large shrimp with a pepper spice;<br>served with bell peppers and white crunchies.</p></div>
    <div class="dish"><div class="dish__head"><span>Cashew Shrimp</span><span>13.95</span></div>
      <p class="dish__desc">Large shrimp with zucchini, onions, and roasted ca-<br>shews in oyster sauce.</p></div>
    <div class="dish"><div class="dish__head"><span>Orange Shrimp</span><span>13.95</span></div>
      <p class="dish__desc">Large crispy shrimp with onions and red and green<br>bell peppers in a sweet orange sauce.</p></div>
  </section>

  <div class="brand brand--left"><span class="brand__mark"></span>LO MARA</div>
  <div class="brand brand--right"><span class="brand__mark"></span>LO MARA</div>
</main>
</body>
</html>
```